Law Firm Website

We are a small California based law firm specializing in business, corporate and litigation matters. We need to have our website redesigned. We are looking for a new and fresh look for our site, keeping in mind that we are a law firm.
What we don't want:
**the traditional "gavel" and "scales of justice" look
**anything too crazy
What we do want:
**sophisticated yet modern and fresh corporate look and feel
**samples of websites we really like:
http://www.tarnwellhope.example
http://www.marrowgate.example/
we also like:
http://www.fenwoodastley.example/
http://www.qz.example/
http://www.brenhollow.example/
http://www.pvdn.example
http://www.nqrlaw.example/
The content will be whatever is currently on our website (www.okabelawgroup.example). We will be selecting the winner based on originality and keeping the above requirements in mind. Please note that the photos that you use will be the ones that we will be using, so choose wisely because the photos will make a difference.
Target Market(s)
Corporate clients
Industry/Entity Type
Law Firm
Look and feel

```html
<!DOCTYPE html>
<html lang="en">
<head>
<meta charset="utf-8">
<title>Okabe Law Group, LLP</title>
<link rel="stylesheet" href="https://fonts.googleapis.com/css2?family=Open+Sans:wght@400;600;700&display=swap">
<style>
:root{
  --ink:#111111;
  --text:#2b2b2b;
  --muted:#6a6a6a;
  --line:#d6d3cf;
  --paper:#ffffff;
  --hero-a:#f4f1ed;
  --hero-b:#e9e4de;
  --brand:#1f7fd6;
  --field-border:#cfcfcf;
}
*{box-sizing:border-box;margin:0;padding:0}
html,body{width:1200px;height:930px;overflow:hidden}
body{font-family:"Open Sans",Arial,sans-serif;color:var(--text);background:var(--paper);position:relative}
.site-header{position:absolute;left:0;top:0;width:1200px;height:166px;background:var(--paper);border-bottom:1px solid var(--line)}
.brand{position:absolute;left:112px;top:96px;display:flex;align-items:center;gap:10px}
.brand-mark{width:22px;height:22px;background:var(--brand)}
.brand-name{font-weight:700;font-size:24px;color:var(--ink);letter-spacing:-0.3px}
.toll-free{position:absolute;right:111px;top:45px;font-size:15px;font-weight:600;color:#555}
.toll-free b{color:var(--ink);font-weight:700}
.social{display:flex;gap:7px}
.social span{width:36px;height:36px;border-radius:50%;background:var(--ink);display:block}
.site-header .social{position:absolute;right:111px;top:82px}
.main-nav{position:absolute;right:111px;top:140px;display:flex}
.main-nav a{font-size:14.5px;font-weight:600;color:var(--ink);text-decoration:none;padding:0 9px;border-right:1px solid #999;line-height:26px}
.main-nav a:first-child{color:#555}
.main-nav a:last-child{border-right:none;padding-right:2px}
.hero{position:absolute;left:0;top:167px;width:1200px;height:686px;background:radial-gradient(ellipse at 50% 30%,var(--hero-a),var(--hero-b))}
.hero-copy{position:absolute;left:182px;top:108px;width:470px}
.hero-copy h1{font-size:31px;font-weight:700;line-height:34px;color:var(--ink);text-transform:uppercase;letter-spacing:-0.2px}
.hero-copy p{margin-top:10px;font-size:12px;line-height:22px;text-transform:uppercase;color:#333}
.hero-art{position:absolute;left:708px;top:43px;width:300px;height:255px;border-radius:6px;background:linear-gradient(180deg,#e5e0da,#d8d2cb)}
.slide-arrow{position:absolute;top:193px;width:38px;height:38px}
.slide-arrow.prev{left:109px}
.slide-arrow.next{left:1052px}
.card{position:absolute;top:354px;width:318px;height:320px;background:var(--paper);border:1px solid #e2dfdb;border-radius:4px;padding:20px 24px}
.card h2{font-size:20px;font-weight:600;color:var(--ink);text-transform:uppercase;margin-top:0;line-height:24px}
.card .icon{position:absolute;right:24px;top:14px;width:32px;height:32px}
.card.practice{left:109px}
.card.blog{left:447px}
.card.ask{left:784px}
.practice ul{list-style:none;margin-top:10px}
.practice li{position:relative;padding-left:16px;font-size:13px;line-height:20.5px;margin-bottom:11.5px}
.practice li::before{content:"";position:absolute;left:1px;top:8px;width:7px;height:7px;border-radius:50%;background:#aaa}
.blog-list{margin-top:10px}
.blog-item{font-size:13px;line-height:20.5px;margin-bottom:8px}
.blog-item time{display:block;font-size:10.5px;color:var(--muted);line-height:16px;margin-top:2px}
.btn{position:absolute;left:25px;bottom:18px;background:var(--ink);color:#fff;font-size:13.5px;padding:4px 15px;border-radius:3px;text-decoration:none}
.ask-form{margin-top:12px;display:flex;flex-direction:column;gap:11px}
.field{height:30px;border:1px solid var(--field-border);border-radius:3px;font-size:12px;color:#444;padding:6px 12px;background:linear-gradient(#fff,#f6f6f6);position:relative}
.field.select::after{content:"";position:absolute;right:10px;top:11px;border-left:5px solid transparent;border-right:5px solid transparent;border-top:8px solid #555}
.field.area{height:74px}
.go{position:absolute;right:20px;top:18px;width:40px;height:40px;border-radius:50%;background:var(--ink);color:#fff;font-size:14px;font-weight:600;display:flex;align-items:center;justify-content:center}
.site-footer{position:absolute;left:0;top:853px;width:1200px;height:77px;background:var(--paper);border-top:1px solid var(--line)}
.foot-nav{position:absolute;left:109px;top:17px;font-size:12.5px;color:#555}
.foot-nav span{margin:0 9px;color:#777}
.copyright{position:absolute;left:109px;top:41px;font-size:11.5px;color:#555}
.site-footer .social{position:absolute;right:111px;top:25px}
</style>
</head>
<body>
<header class="site-header">
  <div class="brand"><span class="brand-mark"></span><span class="brand-name">Okabe Law Group, LLP</span></div>
  <div class="toll-free">TOLL FREE: <b>555&nbsp;&nbsp;01234 56789</b></div>
  <div class="social" aria-label="Social links"><span></span><span></span><span></span></div>
  <nav class="main-nav"><a href="#">O NAS</a><a href="#">INDYWIDUALNI</a><a href="#">KORPORACYJNI</a><a href="#">KONTAKT</a></nav>
</header>

<section class="hero">
  <svg class="slide-arrow prev" viewBox="0 0 38 38"><circle cx="19" cy="19" r="17" fill="none" stroke="#222" stroke-width="2.5"/><path d="M22 11 L14 19 L22 27" fill="none" stroke="#222" stroke-width="3"/></svg>
  <div class="hero-copy">
    <h1>Lorem ipsum is simply dummy text of the printing and typesetting industry</h1>
    <p>Lorem ipsum is simply dummy text of the printing and typesetting industry. Lorem ipsum has been the industry's standard dummy text ever since the 1500s,</p>
  </div>
  <div class="hero-art" role="img" aria-label="Silhouette of balance scales"></div>
  <svg class="slide-arrow next" viewBox="0 0 38 38"><circle cx="19" cy="19" r="17" fill="none" stroke="#222" stroke-width="2.5"/><path d="M16 11 L24 19 L16 27" fill="none" stroke="#222" stroke-width="3"/></svg>

  <article class="card practice">
    <h2>Practice Area</h2>
    <span class="icon" role="img" aria-label="Gavel icon" style="background:#bdbdbd;border-radius:4px;width:28px;height:28px;top:16px"></span>
    <ul>
      <li>Lorem Ipsum is simply dummy text of the printing and typesetting industry</li>
      <li>Lorem Ipsum is simply dummy text of the printing and typesetting industry</li>
      <li>Lorem Ipsum is simply dummy text of the printing and typesetting industry</li>
      <li>Lorem Ipsum is simply dummy text of the printing and typesetting industry</li>
    </ul>
    <a class="btn" href="#">Learn More</a>
  </article>

  <article class="card blog">
    <h2>Our Blog</h2>
    <svg class="icon" viewBox="0 0 32 32"><rect x="5" y="4" width="24" height="18" rx="2" fill="none" stroke="#333" stroke-width="3"/><path d="M9 22 L9 29 L15 22" fill="#333"/><rect x="2" y="6" width="5" height="16" fill="#333"/></svg>
    <div class="blog-list">
      <div class="blog-item">Lorem Ipsum is simply dummy text of the printing and typesetting industry<time>06:44:45 AM November 19th</time></div>
      <div class="blog-item">Lorem Ipsum is simply dummy text of the printing and typesetting industry<time>06:44:45 AM November 19th</time></div>
      <div class="blog-item">Lorem Ipsum is simply dummy text of the printing and typesetting industry<time>06:44:45 AM November 19th</time></div>
    </div>
    <a class="btn" href="#">Learn More</a>
  </article>

  <article class="card ask">
    <h2>Ask a Question</h2>
    <svg class="icon" viewBox="0 0 32 32"><path d="M3 13 L16 3 L29 13 L29 29 L3 29 Z" fill="#444"/><rect x="8" y="8" width="16" height="12" fill="#fff"/><path d="M3 13 L16 22 L29 13 L29 29 L3 29 Z" fill="#555"/><path d="M3 29 L16 20 L29 29" fill="none" stroke="#fff" stroke-width="1.5"/></svg>
    <div class="ask-form">
      <div class="field">Name</div>
      <div class="field">Phone Number</div>
      <div class="field">Email Address</div>
      <div class="field select">Service</div>
      <div class="field area">Question<span class="go">GO</span></div>
    </div>
  </article>
</section>

<footer class="site-footer">
  <div class="foot-nav">O NAS<span>|</span>INDYWIDUALNI<span>|</span>KORPORACYJNI<span>|</span>KONTAKT</div>
  <div class="copyright">Copyright © 2014 lawfirm. All Rights Reserved</div>
  <div class="social" aria-label="Social links"><span></span><span></span><span></span></div>
</footer>
</body>
</html>
```